Meridale Staffing Website

My business has been word of mouth over the last 3 years and has grown. Now I need a website for additional marketing as we have new clients asking for a website.

You have already completed my Logo during an earlier project. I have attached the logo.

We do Staff Augmentation and Operation Support.

What is that?
Staff augmentation is an outsourcing strategy that allows companies to fill specific, temporary roles to achieve business objectives. This staffing method complements existing teams with specific talent, enhancing business capabilities or filling gaps left by members on extended leave.

We work alongside the internal recruiting team to assist clients to meet and exceed financial goals.

```html
<!DOCTYPE html>
<html lang="en">
<head>
<meta charset="utf-8">
<title>Meridale Staffing</title>
<link href="https://fonts.googleapis.com/css2?family=Jost:wght@400;500;600&display=swap" rel="stylesheet">
<style>
:root{
  --navy:#0e416b;
  --navy-dark:#0a3356;
  --grey:#6b6b6b;
  --ink:#2b2b2b;
  --muted:#5a5a5a;
  --light:#eef0f3;
  --line:#c9d8e1;
  --black:#050505;
  --white:#ffffff;
}
*{margin:0;padding:0;box-sizing:border-box}
html,body{width:1200px;height:4532px;overflow:hidden;background:var(--white)}
body{position:relative;font-family:"Jost",sans-serif;color:var(--ink)}
.abs{position:absolute}
svg{display:block}

/* hero */
.hero{left:0;top:0;width:1200px;height:800px}
.hero-photo{left:0;top:0;width:1200px;height:765px;background:linear-gradient(180deg,#6e7479 0%,#8d8d8a 45%,#5a5d61 100%)}
.hero-shade{left:0;top:0;width:1200px;height:765px;background:linear-gradient(90deg,rgba(0,0,0,.35),rgba(0,0,0,.05) 60%,rgba(0,0,0,.15))}
.brand{display:flex;align-items:center;gap:10px;color:var(--white);font-weight:500;font-size:27px;line-height:1;letter-spacing:.5px}
.brand-dot{width:36px;height:36px;border-radius:50%;border:4px solid var(--white)}
.brand small{display:block;font-size:16px;letter-spacing:1px;margin-top:2px}
.nav{left:405px;top:62px;display:flex;gap:30px;font-size:14px;color:var(--white);letter-spacing:.3px}
.nav .active{border-bottom:3px solid var(--white);padding-bottom:5px}
.login{left:990px;top:53px;width:98px;height:38px;border-radius:19px;background:var(--navy);color:var(--white);font-size:14px;display:flex;align-items:center;justify-content:center}
.hero-title{left:111px;top:296px;color:var(--white);font-size:35px;line-height:41px;font-weight:500;letter-spacing:.5px}
.btn{border-radius:20px;background:var(--navy);color:var(--white);font-size:14px;display:flex;align-items:center;justify-content:center;letter-spacing:.3px}
.hero-btn{left:114px;top:394px;width:156px;height:36px}
.slide-dot{width:11px;height:11px;border-radius:50%;background:var(--white)}
.slide-num{left:1124px;top:305px;width:34px;height:34px;border-radius:50%;background:var(--navy);color:var(--white);font-size:16px;display:flex;align-items:center;justify-content:center}

/* headings */
.mark{width:36px;height:36px;border-radius:50%;background:var(--navy)}
.h2{width:1200px;left:0;text-align:center;font-size:35px;font-weight:400;letter-spacing:.5px;color:var(--ink)}
.h2 b{font-weight:500;color:var(--navy)}
.lead{width:1200px;left:0;text-align:center;font-size:14.5px;line-height:26px;color:var(--muted)}

/* services */
.service{width:172px;height:268px}
.service-label{position:absolute;left:64px;width:108px;top:168px;text-align:center;color:var(--white);font-size:14px;line-height:19px;font-weight:500}
.service svg.icon{position:absolute;left:88px;top:90px}

/* about */
.about-text{left:622px;top:1539px;width:463px;font-size:14.5px;line-height:21.2px;color:var(--muted);text-align:justify}
.about-h{left:622px;top:1435px;font-size:35px;line-height:42px;color:var(--ink)}
.about-h b{font-weight:500;color:var(--navy)}
.about-btn{left:622px;top:1792px;width:158px;height:36px}
.about-emblem{left:180px;top:1420px;width:360px;height:360px;border-radius:50%;background:var(--navy);display:flex;align-items:center;justify-content:center;color:var(--white);font-size:30px;font-weight:500}
.about-bg{left:0;top:1330px;width:1200px;height:540px;background:linear-gradient(90deg,#dfe2e6,#eef0f3 45%,#dde1e6)}

/* why */
.why-item{font-size:14.5px;line-height:26px;color:var(--muted);width:240px}
.why-item.left{text-align:right}
.why-dot{width:13px;height:13px;border-radius:50%;background:var(--navy)}

/* team */
.team-card{width:227px;height:324px;background:var(--white);border-radius:4px}
.team-photo{position:absolute;left:5px;top:5px;width:217px;height:222px;background:linear-gradient(180deg,#e8e8e8,#bfbfbf)}
.team-name{position:absolute;top:240px;width:100%;text-align:center;font-size:23px;color:var(--ink)}
.team-role{position:absolute;top:275px;width:100%;text-align:center;font-size:14.5px;line-height:21px;color:var(--muted)}
.view-btn{left:521px;top:3132px;width:158px;height:38px;background:var(--white);color:var(--navy);font-size:14px;font-weight:500;border-radius:19px;display:flex;align-items:center;justify-content:center}

/* testimonials */
.testi-photo{left:171px;top:3422px;width:350px;height:292px;border-radius:90px 120px 80px 110px;background:linear-gradient(135deg,#2e5d85,#9aa4ad 55%,#d8d8d6)}
.quote{left:600px;top:3470px;width:480px;font-size:15px;line-height:22px;font-style:italic;color:var(--muted)}
.avatar{left:598px;top:3572px;width:64px;height:64px;border-radius:50%;background:linear-gradient(180deg,#c9b8a8,#5b4b44)}
.t-name{left:679px;top:3584px;font-size:22px;color:var(--navy)}
.t-co{left:677px;top:3614px;font-size:14px;color:var(--ink)}
.t-dot{width:12px;height:12px;border-radius:50%;background:#b8b8b8}

/* partners */
.partner{width:186px;height:84px;background:var(--white);box-shadow:0 3px 10px rgba(0,0,0,.12);display:flex;align-items:center;justify-content:center;gap:8px;font-size:13px;font-weight:500;color:var(--navy)}
.partner i{width:18px;height:18px;border-radius:50%;background:var(--navy);display:block}
.chev{font-size:28px;color:var(--navy)}

/* footer */
.footer-bg{left:0;top:3985px;width:1200px;height:547px;background:var(--black)}
.f-brand{left:111px;top:4190px}
.f-text{left:110px;top:4280px;width:330px;font-size:13.5px;line-height:21.5px;color:var(--white)}
.f-head{font-size:21px;color:var(--white);font-weight:500}
.f-list{list-style:none;font-size:14px;line-height:21.5px;color:var(--white)}
.f-list.arrow li::before{content:"»";color:#777;margin-right:12px}
.copy{left:0;width:1200px;top:4458px;text-align:center;font-size:13px;color:var(--white)}
</style>
</head>
<body>

<!-- HERO -->
<section class="hero abs">
  <div class="hero-photo abs" role="img" aria-label="Team of smiling business professionals standing in a bright office"></div>
  <div class="hero-shade abs"></div>
  <div class="brand abs" style="left:109px;top:40px"><span class="brand-dot"></span><span>MERIDALE<small>STAFFING</small></span></div>
  <nav class="nav abs"><span class="active">HOME</span><span>ABOUT</span><span>SERVICES</span><span>TESTIMONIALS</span><span>BLOG</span><span>CONTACT US</span></nav>
  <div class="login abs">LOGIN</div>
  <h1 class="hero-title abs" style="font-weight:500">WE DO STAFF AUGMENTATION<br>AND OPERATION SUPPORT</h1>
  <div class="btn hero-btn abs">GET STARTED</div>
  <div class="slide-num abs">1</div>
  <div class="slide-dot abs" style="left:1135px;top:359px"></div>
  <div class="slide-dot abs" style="left:1135px;top:394px"></div>
  <div class="slide-dot abs" style="left:1135px;top:428px"></div>
  <svg class="abs" style="left:0;top:600px" width="1200" height="200" viewBox="0 600 1200 200">
    <path d="M0 752 Q600 512 1200 752 L1200 765 Q600 537 0 765 Z" fill="var(--navy)"/>
    <path d="M0 765 Q600 537 1200 765 L1200 800 L0 800 Z" fill="#fff"/>
    <circle cx="600" cy="648" r="27" fill="#fff"/>
    <path d="M600 634 V661 M591 652 L600 661 L609 652" stroke="#222" stroke-width="2.5" fill="none"/>
  </svg>
</section>

<!-- WHAT WE DO -->
<div class="mark abs" style="left:582px;top:730px"></div>
<h2 class="h2 abs" style="top:775px">WHAT <b>WE DO</b></h2>
<p class="lead abs" style="top:828px">Lorem ipsum dolor sit amet, consectetur adipiscing elit, sed do eiusmod tempor incididunt ut labore et dolore<br>magna aliqua Lorem ipsum dolor sit amet, consectetur adipiscing elit</p>

<div class="service abs" style="left:109px;top:911px">
  <svg width="172" height="268"><path d="M0 0 C80 -4 172 60 172 150 L172 268 L64 268 L64 150 C64 80 42 30 0 0 Z" fill="var(--grey)"/></svg>
  <svg class="icon" width="66" height="66" viewBox="0 0 66 66" fill="none" stroke="#fff" stroke-width="2"><circle cx="33" cy="22" r="9"/><circle cx="33" cy="22" r="3"/><path d="M6 52 L20 44 H40 L58 36 M20 44 L30 50 H46"/></svg>
  <div class="service-label">Handling of work project</div>
</div>
<div class="service abs" style="left:311px;top:911px">
  <svg width="172" height="268"><path d="M0 0 C80 -4 172 60 172 150 L172 268 L64 268 L64 150 C64 80 42 30 0 0 Z" fill="var(--navy)"/></svg>
  <svg class="icon" width="66" height="66" viewBox="0 0 66 66" fill="none" stroke="#fff" stroke-width="2"><path d="M30 6 H52 V30 H30 Z M38 6 V18"/><circle cx="26" cy="44" r="9"/><circle cx="46" cy="50" r="6"/></svg>
  <div class="service-label">Feedback mechanism</div>
</div>
<div class="service abs" style="left:514px;top:911px">
  <svg width="172" height="268"><path d="M0 0 C80 -4 172 60 172 150 L172 268 L64 268 L64 150 C64 80 42 30 0 0 Z" fill="var(--grey)"/></svg>
  <svg class="icon" width="66" height="66" viewBox="0 0 66 66" fill="none" stroke="#fff" stroke-width="2"><path d="M10 6 H40 V58 H10 Z M16 16 H32 M16 26 H28 M16 36 H26"/><circle cx="42" cy="36" r="10"/><path d="M49 43 L58 52 M38 36 L41 39 L46 33"/></svg>
  <div class="service-label">Background verification</div>
</div>
<div class="service abs" style="left:716px;top:911px">
  <svg width="172" height="268"><path d="M0 0 C80 -4 172 60 172 150 L172 268 L64 268 L64 150 C64 80 42 30 0 0 Z" fill="var(--grey)"/></svg>
  <svg class="icon" width="66" height="66" viewBox="0 0 66 66" fill="none" stroke="#fff" stroke-width="2"><path d="M12 30 V10 M8 14 L12 10 L16 14 M26 26 V6 M22 10 L26 6 L30 10 M40 26 V6 M36 10 L40 6 L44 10 M54 30 V10 M50 14 L54 10 L58 14"/><circle cx="19" cy="40" r="5"/><circle cx="33" cy="40" r="5"/><circle cx="47" cy="40" r="5"/><path d="M10 58 V52 H28 V58 M24 58 V52 H42 V58 M38 58 V52 H56 V58"/></svg>
  <div class="service-label">Performance management</div>
</div>
<div class="service abs" style="left:918px;top:911px">
  <svg width="172" height="268"><path d="M0 0 C80 -4 172 60 172 150 L172 268 L64 268 L64 150 C64 80 42 30 0 0 Z" fill="var(--grey)"/></svg>
  <svg class="icon" width="66" height="66" viewBox="0 0 66 66" fill="none" stroke="#fff" stroke-width="2"><circle cx="33" cy="20" r="9"/><path d="M8 20 H20 M46 20 H58 M12 16 L8 20 L12 24 M54 16 L58 20 L54 24"/><circle cx="20" cy="44" r="4"/><circle cx="33" cy="44" r="4"/><circle cx="46" cy="44" r="4"/><path d="M12 56 V52 H28 V56 M25 56 V52 H41 V56 M38 56 V52 H54 V56"/></svg>
  <div class="service-label">Behavioral development</div>
</div>

<!-- ABOUT -->
<div class="about-bg abs" role="img" aria-label="Faded city skyline with business people in the background"></div>
<svg class="abs" style="left:0;top:1260px" width="1200" height="740" viewBox="0 1260 1200 740">
  <path d="M0 1260 H1200 V1430 Q600 1170 0 1430 Z" fill="#fff"/>
  <path d="M0 1430 Q600 1170 1200 1430 L1200 1410 Q600 1230 0 1430 Z" fill="var(--navy)"/>
  <path d="M0 1830 Q600 2100 1200 1830 V2000 H0 Z" fill="#fff"/>
  <path d="M0 1830 Q600 2100 1200 1830 L1200 1815 Q600 2020 0 1830 Z" fill="var(--navy)"/>
</svg>
<div class="about-emblem abs">Meridale Staffing</div>
<div class="mark abs" style="left:622px;top:1390px"></div>
<h2 class="about-h abs" style="font-weight:400">ABOUT <b>US</b><br><b>MERIDALE STAFFING</b></h2>
<p class="about-text abs">Lorem ipsum dolor sit amet, consectetur adipiscing elit, sed do eiusmod tempor incididunt ut labore et dolore magna aliqua. Ut enim ad minim veniam, quis nostrud exercitation ullamco laboris nisi ut aliquip ex ea commodo consequat. Duis aute irure dolor in reprehenderit in voluptate velit esse cillum dolore eu fugiat nulla pariatur. Excepteur sint occaecat cupidatat non proident, sunt in culpa qui officia deserunt mollit anim id est laborum.Lorem ipsum dolor sit amet, consectetur adipiscing elit, sed do eiusmod tempor incididunt ut labore et dolore magna aliqua. Ut enim ad minim veniam, quis nostrud exercitation ullamco laboris nisi ut aliquip ex ea commodo consequat.</p>
<div class="btn about-btn abs">LEARN MORE &#9654;</div>

<!-- WHY CHOOSE US -->
<div class="mark abs" style="left:582px;top:2024px"></div>
<h2 class="h2 abs" style="top:2072px">WHY <b>CHOOSE US</b></h2>
<p class="lead abs" style="top:2130px">Lorem ipsum dolor sit amet, consectetur adipiscing elit, sed do eiusmod tempor incididunt ut labore et dolore<br>magna aliqua Lorem ipsum dolor sit amet, consectetur adipiscing elit</p>
<svg class="abs" style="left:340px;top:2200px" width="520" height="300" viewBox="0 0 520 300">
  <path d="M18 298 A242 242 0 0 1 502 298" fill="none" stroke="var(--line)" stroke-width="4"/>
  <path d="M38 298 A222 222 0 0 1 482 298" fill="none" stroke="var(--line)" stroke-width="9"/>
</svg>
<div class="abs" style="left:520px;top:2310px;width:160px;height:160px;border-radius:50%;background:var(--navy);display:flex;align-items:center;justify-content:center;color:#fff;font-size:18px;font-weight:500">Meridale</div>
<div class="why-dot abs" style="left:415px;top:2277px"></div>
<div class="why-dot abs" style="left:772px;top:2277px"></div>
<div class="why-dot abs" style="left:352px;top:2380px"></div>
<div class="why-dot abs" style="left:834px;top:2380px"></div>
<p class="why-item left abs" style="left:102px;top:2250px">Lorem ipsum dolor sit amet<br>consectetur adipiscing</p>
<p class="why-item left abs" style="left:38px;top:2353px">Lorem ipsum dolor sit amet<br>consectetur adipiscing</p>
<p class="why-item abs" style="left:860px;top:2250px">Lorem ipsum dolor sit amet<br>consectetur adipiscing</p>
<p class="why-item abs" style="left:912px;top:2353px">Lorem ipsum dolor sit amet<br>consectetur adipiscing</p>
<svg class="abs" style="left:352px;top:2254px" width="40" height="40" viewBox="0 0 40 40" fill="none" stroke="var(--navy)" stroke-width="2"><path d="M6 34 L22 18 M16 8 L32 24 M20 6 L34 20"/></svg>
<svg class="abs" style="left:290px;top:2357px" width="42" height="42" viewBox="0 0 42 42" fill="none" stroke="var(--navy)" stroke-width="2"><path d="M6 36 L36 6 M6 6 L36 36 M4 10 L10 4 M32 38 L38 32"/></svg>
<svg class="abs" style="left:806px;top:2254px" width="40" height="40" viewBox="0 0 40 40" fill="none" stroke="var(--navy)" stroke-width="2"><circle cx="20" cy="12" r="6"/><path d="M8 36 V28 Q20 18 32 28 V36 Z"/></svg>
<svg class="abs" style="left:866px;top:2357px" width="42" height="42" viewBox="0 0 42 42" fill="none" stroke="var(--navy)" stroke-width="2"><circle cx="21" cy="16" r="9"/><circle cx="21" cy="16" r="3"/><path d="M4 36 L14 30 H28 L38 26"/></svg>

<!-- TEAM -->
<svg class="abs" style="left:0;top:2570px" width="1200" height="620" viewBox="0 2570 1200 620">
  <path d="M0 2718 Q600 2454 1200 2718 V3062 Q600 3272 0 3062 Z" fill="var(--navy)"/>
</svg>
<h2 class="h2 abs" style="top:2680px;color:#fff;font-weight:500">OUR TEAM</h2>
<div class="team-card abs" style="left:111px;top:2766px"><div class="team-photo" role="img" aria-label="Portrait of a team member in a suit"></div><div class="team-name">John Doe</div><div class="team-role">Lorem ipsum dolor amet,<br>consectetur</div></div>
<div class="team-card abs" style="left:361px;top:2766px"><div class="team-photo" role="img" aria-label="Portrait of a team member in a suit"></div><div class="team-name">John Doe</div><div class="team-role">Lorem ipsum dolor amet,<br>consectetur</div></div>
<div class="team-card abs" style="left:611px;top:2766px"><div class="team-photo" role="img" aria-label="Portrait of a team member in a blazer"></div><div class="team-name">John Doe</div><div class="team-role">Lorem ipsum dolor amet,<br>consectetur</div></div>
<div class="team-card abs" style="left:860px;top:2766px"><div class="team-photo" role="img" aria-label="Portrait of a team member in a suit"></div><div class="team-name">John Doe</div><div class="team-role">Lorem ipsum dolor amet,<br>consectetur</div></div>
<div class="view-btn abs">VIEW MORE</div>

<!-- TESTIMONIALS -->
<h2 class="h2 abs" style="top:3338px;font-weight:500">TESTIMONIALS</h2>
<div class="testi-photo abs" role="img" aria-label="Cheerful businessman with a laptop and celebrating colleagues"></div>
<p class="quote abs">"Lorem ipsum dolor sit amet, consectetur adipiscing elit, sed do eiusmod tempor incididunt ut labore et dolore magna aliqua. Ut enim ad minim veniam, quis nostrud exercitation ullamco laboris nisi ut aliquip ex ea commodo consequat."</p>
<div class="avatar abs" role="img" aria-label="Client portrait"></div>
<div class="t-name abs">John doe</div>
<div class="t-co abs">Company name</div>
<div class="abs" style="left:598px;top:3659px;display:flex;gap:4px"><span class="t-dot" style="background:#555"></span><span class="t-dot"></span><span class="t-dot"></span><span class="t-dot"></span><span class="t-dot"></span></div>

<!-- PARTNERS -->
<h2 class="h2 abs" style="top:3788px;font-weight:500">OUR PARTNERS</h2>
<div class="chev abs" style="left:50px;top:3880px">&#8249;</div>
<div class="chev abs" style="left:1136px;top:3880px">&#8250;</div>
<div class="partner abs" style="left:111px;top:3859px"><i></i>Crewline</div>
<div class="partner abs" style="left:309px;top:3859px"><i></i>Staffwell</div>
<div class="partner abs" style="left:507px;top:3859px"><i></i>Teamloop</div>
<div class="partner abs" style="left:705px;top:3859px"><i></i>Hireforge</div>
<div class="partner abs" style="left:903px;top:3859px"><i></i>Brightpath</div>

<!-- FOOTER -->
<div class="footer-bg abs"></div>
<svg class="abs" style="left:0;top:3980px" width="1200" height="140" viewBox="0 3980 1200 140">
  <path d="M0 3980 H1200 V3985 Q600 4231 0 3985 Z" fill="#fff"/>
  <path d="M0 3985 Q600 4231 1200 3985 L1200 4000 Q600 4250 0 4000 Z" fill="var(--navy)"/>
</svg>
<div class="brand f-brand abs"><span class="brand-dot"></span><span>MERIDALE<small>STAFFING</small></span></div>
<p class="f-text abs">Lorem ipsum dolor sit amet, consectetur adipis cing elit, sed do eiusmod tempor incididunt ut labore et dolore magna aliqua. Ut enim ad min im veniam, quis nostrud exercitation ullamco laboris nisiut aliquip exeacommodo</p>
<div class="f-head abs" style="left:508px;top:4200px">Quick links</div>
<ul class="f-list arrow abs" style="left:510px;top:4264px"><li>Home</li><li>About us</li><li>Services</li><li>Blog</li><li>Testimonials</li><li>Contact us</li></ul>
<div class="f-head abs" style="left:741px;top:4200px">Help</div>
<ul class="f-list arrow abs" style="left:742px;top:4264px"><li>Privacy policy</li><li>Terms &amp; conditions</li><li>Contact us</li><li>Faq</li><li>Cookies</li><li>Partners</li></ul>
<div class="f-head abs" style="left:994px;top:4200px">Follow us</div>
<ul class="f-list abs" style="left:995px;top:4264px"><li>Newsroom</li><li>Updates</li><li>Network</li><li>Gallery</li><li>Videos</li></ul>
<div class="copy abs">Copyright &copy; 2022 Company name | Privacy Policy | Terms &amp; Conditions</div>

</body>
</html>
```